Stonebrace Business Card Design

The Stonebrace Co is an aggregate (crushing) equipment dealer serving Western Canadian provinces. Stonebrace is a distributor of aggregate equipment for different manufacturers.

We are looking to change and update the existing business card which has been used since the existence of the company. A copy of existing card has been attached for reference. The Stonebrace Co logo we want to remain the same and we want the green color to remain the same.

We are wanting something new with a different look. A refreshing card to show a new modern and updated look. No longer wanting to have the manufacturers on the back of the card but something more like our logo on the back of the card with a statement like "Crushing Solutions"

ideas could be:
- card can be different colors on front and back
- front or reverse of the card could possibly be the green color with the logo in black

Target Market(s)

Owners of Aggregate/Crushing companies

Contact Information for Business Card

see above

Requirements
Must have
• - logo to remain same along with same font within logo
• - green color to remain same
Nice to have
• as noted above under project description
Should not have

```html
<!DOCTYPE html>
<html lang="en">
<head>
<meta charset="utf-8">
<title>Stonebrace Business Card</title>
<link href="https://fonts.googleapis.com/css2?family=Open+Sans:wght@400;700&display=swap" rel="stylesheet">
<style>
  :root {
    --stage: #e4e5e7;
    --card: #0a0a0b;
    --brand-green: #a29c1f;
    --ink-light: #f2f2f2;
    --ink-dark: #0a0a0b;
  }
  * { box-sizing: border-box; margin: 0; padding: 0; }
  html, body { width: 1200px; height: 1200px; overflow: hidden; }
  body {
    background: var(--stage);
    font-family: "Open Sans", sans-serif;
    display: flex; flex-direction: column; align-items: center; justify-content: center;
    gap: 44px;
  }
  .card {
    position: relative;
    width: 900px; height: 514px;
    background: var(--card);
    color: var(--ink-light);
    overflow: hidden;
  }
  .brand { display: flex; align-items: center; gap: 14px; }
  .brand-dot { width: 34px; height: 34px; border-radius: 50%; background: var(--brand-green); }
  .brand-name { font-weight: 700; font-size: 26px; letter-spacing: 1px; color: var(--ink-light); white-space: nowrap; }

  /* Front: brand green with the mark in black */
  .card-front { background: var(--brand-green); color: var(--ink-dark); }
  .card-front .brand {
    position: absolute; top: 170px; left: 0; right: 0;
    flex-direction: column; gap: 22px;
  }
  .card-front .brand-dot { width: 64px; height: 64px; background: var(--ink-dark); }
  .card-front .brand-name { color: var(--ink-dark); font-size: 34px; letter-spacing: 2px; }
  .statement {
    position: absolute; top: 352px; left: 0; right: 0; text-align: center;
    font-size: 18px; letter-spacing: 6px; text-transform: uppercase; color: var(--ink-dark);
  }
  .statement-rule {
    position: absolute; top: 334px; left: 50%; width: 120px; height: 2px;
    margin-left: -60px; background: var(--ink-dark);
  }

  /* Back: contact details */
  .card-back .brand { position: absolute; top: 300px; left: 70px; }
  .card-back .brand-name { font-size: 22px; }
  .arc-graphic { position: absolute; inset: 0; }
  .holder-name {
    position: absolute; top: 90px; left: 420px;
    font-size: 32px; font-weight: 400; color: var(--brand-green);
    text-transform: uppercase; letter-spacing: 1px; white-space: nowrap;
  }
  .contact-line { position: absolute; font-size: 17px; letter-spacing: .5px; white-space: nowrap; }
</style>
</head>
<body>
  <section class="card card-front">
    <div class="brand"><span class="brand-dot"></span><span class="brand-name">THE STONEBRACE CO.</span></div>
    <span class="statement-rule"></span>
    <p class="statement">Crushing Solutions</p>
  </section>

  <section class="card card-back">
    <svg class="arc-graphic" width="900" height="514" viewBox="0 0 900 514" aria-hidden="true">
      <path d="M 364.7 133 A 200 200 0 0 1 458.6 483.2" fill="none" stroke="var(--brand-green)" stroke-width="3"/>
      <g fill="var(--brand-green)">
        <circle cx="444.7" cy="166.2" r="13"/>
        <circle cx="493.8" cy="215.3" r="13"/>
        <circle cx="523.2" cy="278.2" r="13"/>
        <circle cx="529.2" cy="347.4" r="13"/>
        <circle cx="511.3" cy="414.5" r="13"/>
      </g>
      <g fill="none" stroke="var(--card)" stroke-width="1.6">
        <rect x="440.2" y="159.2" width="9" height="14" rx="1.5"/>
        <path d="M487.8 211.3 q2 -3 4 0 l-1 2 q2 4 5 5 l2 -1 q3 2 0 4 q-8 0 -10 -10z"/>
        <rect x="517.2" y="275.2" width="12" height="7"/><rect x="519.7" y="272.2" width="7" height="3"/>
        <rect x="522.2" y="342.4" width="14" height="10"/><path d="M522.2 342.4 l7 6 l7 -6"/>
        <circle cx="511.3" cy="414.5" r="7"/><path d="M504.3 414.5 h14 M511.3 407.5 v14"/>
      </g>
    </svg>
    <h1 class="holder-name">Dale Morven</h1>
    <p class="contact-line" style="top:154px;left:470px">780.555.0142</p>
    <p class="contact-line" style="top:203px;left:519px">780.555.0178</p>
    <p class="contact-line" style="top:266px;left:549px">780.555.0193</p>
    <p class="contact-line" style="top:335px;left:555px">dale@stonebrace.com</p>
    <p class="contact-line" style="top:402px;left:537px">www.stonebrace.ca</p>
    <div class="brand"><span class="brand-dot"></span><span class="brand-name">THE STONEBRACE CO.</span></div>
  </section>
</body>
</html>
```